Vensol Holdings Web Design

Vensol Holdings Limited Shenzhen

This project is a 10 page launch website.
Our client is seeking a contemporary homepage design for a Holdings company. Once we are happy with the homepage design and select designer we will request a secondary page design.

Please see attached company LOGO for an idea of style, it incorporates the traditional Chinese furniture lattice work. The Corvel crest website is one of our clients favorite so we would like to see a similar homepage design to this website.

Use the websites below for reference purpose. The first two are Chinese and the second two are international. We would like to see elements of both but more focus on international design.

http://www.evergrande.com/http://www.taurenfield.com/pub/default.aspx http://www.corvelcrest.com/zh/maldives_lorinhaven/
http://www.quelba-studio.com
http://media-cache-ex0.snapvalu.com/originals/71/a3/19/71a319c5b2d04e8f6a17c3b9e5d0f4a1.jpg

Company Background
VENSOL HOLDINGS, located in Qianhai, China, is a new real-estate project operator, structuring urban-rural real-estate investment and development, and industrial fund investment. The company also invests in supply chain management and supporting infrastructures. To create new spaces and livable cities Vensol Holdings develop win-win strategic partnerships with a number of institutions. Currently cooperating with Tianjing North Lumore, China urban and rural integrated demonstration.

Target Market(s)

B2B property investment. Target market customers are senior level management/decision makers of large corporations. Focusing geographically on the domestic market first and expanding internationally in 2nd and 3rd years.

Industry/Entity Type

Investment

Requirements
Must have
• Since this is a new company, we would like to the website representing growth and power, E.g. like a growing tree.
Should not have
• Low-level vectors such as curency symbols, American dollar.

```html
<!DOCTYPE html>
<html lang="en">
<head>
<meta charset="utf-8">
<title>Vensol Holdings</title>
<link rel="stylesheet" href="https://fonts.googleapis.com/css2?family=Arimo:wght@400;700&family=Oswald:wght@500;700&family=Ubuntu:ital,wght@0,400;0,500;0,700;1,400&display=swap">
<style>
:root{
  --gold:#c8901a;
  --gold-light:#e0a93a;
  --orange:#f6a01a;
  --orange-dark:#e38a08;
  --ink:#2b2b2b;
  --text:#555;
  --muted:#888;
  --paper:#f4f4f4;
  --white:#fff;
  --dark:#1d1f22;
  --footer:#2a2a2a;
  --footer-deep:#1b1b1b;
  --line:#d9d9d9;
  --blue:#2a6ebb;
}
*{box-sizing:border-box;margin:0;padding:0}
html,body{width:1200px;height:2246px;overflow:hidden}
body{font-family:"Ubuntu",sans-serif;color:var(--text);background:var(--paper);position:relative}
.abs{position:absolute}

/* header */
.site-header{position:absolute;left:0;top:0;width:1200px;height:107px;background:var(--white);border-bottom:1px solid #e4e4e4}
.brand{position:absolute;left:146px;top:14px;width:120px;text-align:center}
.brand-mark{width:54px;height:54px;border-radius:50%;background:var(--gold);margin:0 auto 6px}
.brand-name{font-family:"Ubuntu",sans-serif;font-size:12px;font-weight:500;color:var(--gold);letter-spacing:.5px}
.search{position:absolute;left:730px;top:8px;width:240px;height:32px;border:1px solid #ccc;border-radius:3px;background:#fff;box-shadow:0 1px 3px rgba(0,0,0,.12)}
.search span{position:absolute;left:12px;top:8px;font-family:"Arimo",sans-serif;font-size:12px;color:#333}
.search svg{position:absolute;right:10px;top:8px}
.lang{position:absolute;left:982px;top:8px;width:60px;height:32px;border:1px solid #ccc;border-radius:3px;background:#fafafa}
.lang i{position:absolute;left:9px;top:11px;width:18px;height:11px;background:#c9c3d8;border:1px solid #b8b0c8}
.lang svg{position:absolute;right:9px;top:13px}
.nav a{position:absolute;top:62px;height:34px;line-height:34px;font-family:"Arimo",sans-serif;font-weight:700;font-size:16px;color:#333;text-decoration:none}
.nav .current{left:537px;width:86px;text-align:center;color:#fff;border-radius:3px;background:linear-gradient(#fbb53a,var(--orange-dark));box-shadow:0 1px 2px rgba(0,0,0,.25)}

/* hero */
.hero{position:absolute;left:0;top:107px;width:1200px;height:633px;background:linear-gradient(180deg,#5a3f26 0%,#3a2a1f 45%,#1d1812 100%)}
.hero-title{position:absolute;left:0;width:1200px;top:548px;text-align:center;font-family:"Arimo",sans-serif;font-weight:700;font-size:80px;color:#fff;letter-spacing:1px;text-shadow:0 3px 6px rgba(0,0,0,.6)}
.hero-sub{position:absolute;left:0;width:1200px;top:646px;text-align:center;font-family:"Arimo",sans-serif;font-size:39px;color:#fff;text-shadow:0 2px 4px rgba(0,0,0,.6)}
.dots{position:absolute;display:flex;gap:6px}
.dots i{width:8px;height:8px;border-radius:50%;background:#fff}
.dots i.on{background:var(--gold)}

/* intro */
.intro-title{position:absolute;left:150px;top:797px;font-family:"Oswald",sans-serif;font-weight:700;font-size:38px;color:var(--ink);letter-spacing:.5px}
.intro-rule{position:absolute;left:150px;top:854px;width:452px;height:1px;background:var(--line)}
.intro-rule b{position:absolute;left:0;top:-1px;width:78px;height:3px;background:var(--gold)}
.intro-text{position:absolute;left:150px;top:886px;width:452px;font-size:13.5px;line-height:21px;color:var(--text)}
.read-more{position:absolute;left:150px;top:1058px;font-size:13px;color:var(--blue)}

.tabs{position:absolute;left:670px;top:803px}
.tab{position:absolute;top:0;height:32px;line-height:32px;font-family:"Arimo",sans-serif;font-weight:700;font-size:14px;text-align:center;border-radius:3px 3px 0 0}
.tab-news{left:0;width:80px;background:var(--gold);color:#fff}
.tab-awards{left:84px;width:188px;background:#ddd;color:#666}
.news-box{position:absolute;left:670px;top:835px;width:378px;height:264px;background:#fff;border:1px solid var(--gold-light);border-radius:0 3px 3px 3px}
.news-item{position:absolute;left:14px;width:348px}
.news-thumb{position:absolute;left:0;top:0;width:47px;height:47px;border-radius:3px}
.news-body{position:absolute;left:68px;top:0;width:280px}
.news-body h4{font-size:14.5px;font-weight:700;color:var(--ink);margin-bottom:4px}
.news-item.first h4{color:var(--gold)}
.news-body small{display:block;font-size:9.5px;color:#999;margin-bottom:5px}
.news-body p{font-size:12.5px;line-height:18px;color:#777}
.news-sep{position:absolute;left:14px;top:128px;width:348px;height:1px;background:#e6e6e6}

/* feature */
.feature{position:absolute;left:0;top:1161px;width:1200px;height:494px;background:linear-gradient(90deg,#2a2d31,#15171a 50%,#25282c)}
.feature-title{position:absolute;left:150px;top:97px;font-family:"Oswald",sans-serif;font-weight:700;font-size:31px;color:var(--gold-light)}
.feature-sub{position:absolute;left:150px;top:170px;font-size:18px;font-weight:700;color:#fff}
.feature-text{position:absolute;left:150px;top:203px;width:260px;font-size:13.5px;line-height:21px;color:#ccc}
.feature-text p+p{margin-top:21px}
.feature-media{position:absolute;left:434px;top:106px;width:614px;height:290px;border-radius:3px;background:linear-gradient(180deg,#8fb0c4 0%,#c86a6a 35%,#5e8f3a 65%,#3f6b2a 100%);box-shadow:0 4px 14px rgba(0,0,0,.6)}

/* testimonial */
.quote-mark{position:absolute;left:150px;top:1705px;font-family:"Oswald",sans-serif;font-size:80px;line-height:80px;color:#cfcfcf}
.quote-text{position:absolute;left:215px;top:1716px;width:835px;font-style:italic;font-size:13px;line-height:22.5px;color:#666}
.quote-rule{position:absolute;left:215px;top:1803px;width:833px;height:1px;background:#d0d0d0}
.quote-notch{position:absolute;left:235px;top:1803px}
.avatar{position:absolute;left:220px;top:1830px;width:78px;height:78px;border-radius:50%;background:linear-gradient(#cfd6de,#6d7c8c);border:3px solid #fff;box-shadow:0 1px 4px rgba(0,0,0,.3)}
.quote-name{position:absolute;left:328px;top:1858px;font-family:"Oswald",sans-serif;font-weight:500;font-size:17px;color:var(--gold)}
.quote-role{position:absolute;left:330px;top:1884px;font-size:12.5px;font-weight:500;color:#777}
.rings{position:absolute;left:1000px;top:1892px;display:flex;gap:4px}
.rings i{width:9px;height:9px;border-radius:50%;border:1px solid #aaa}
.rings i.on{background:var(--gold);border-color:var(--gold)}

/* footer */
.site-footer{position:absolute;left:0;top:1990px;width:1200px;height:209px;background:var(--footer);border-top:3px solid #3a3a3a}
.footer-col{position:absolute;top:28px}
.footer-col h5{font-family:"Oswald",sans-serif;font-weight:500;font-size:19px;color:var(--gold-light);margin-bottom:17px}
.footer-col ul{list-style:none}
.footer-col li{font-size:11.5px;line-height:20.5px;color:#ccc;padding-left:15px;position:relative}
.footer-col li::before{content:"";position:absolute;left:0;top:9px;width:4px;height:4px;border-radius:50%;background:#bbb}
.footer-divider{position:absolute;top:12px;width:1px;height:180px;background:#444}
.subscribe p{font-size:11.5px;line-height:21px;color:#ccc;width:440px}
.sub-input{position:absolute;left:11px;top:140px;width:331px;height:32px;background:#fff;border-radius:2px;font-size:11.5px;color:#777;line-height:32px;padding-left:10px}
.sub-btn{position:absolute;left:354px;top:140px;width:78px;height:32px;background:linear-gradient(#f9ad2c,var(--orange-dark));border-radius:2px;font-size:11px;color:#333;text-align:center;line-height:32px}
.bottom-bar{position:absolute;left:0;top:2199px;width:1200px;height:47px;background:var(--footer-deep)}
.bottom-bar span{position:absolute;left:150px;top:16px;font-size:11.5px;color:#bbb}
.social{position:absolute;top:8px;width:30px;height:30px;border-radius:50%}
</style>
</head>
<body>

<header class="site-header">
  <div class="brand">
    <div class="brand-mark"></div>
    <div class="brand-name">Vensol Holdings</div>
  </div>
  <div class="search"><span>Search</span>
    <svg width="14" height="14" viewBox="0 0 14 14"><circle cx="6" cy="6" r="4.5" fill="none" stroke="#333" stroke-width="1.8"/><line x1="9.3" y1="9.3" x2="13" y2="13" stroke="#333" stroke-width="2"/></svg>
  </div>
  <div class="lang"><i></i><svg width="9" height="6" viewBox="0 0 9 6"><path d="M0 0h9L4.5 6z" fill="#555"/></svg></div>
  <nav class="nav">
    <a class="current" href="#">HOME</a>
    <a style="left:655px" href="#">ABOUT</a>
    <a style="left:756px" href="#">SERVICES</a>
    <a style="left:880px" href="#">BLOG</a>
    <a style="left:972px" href="#">CONTACT</a>
  </nav>
</header>

<section class="hero" role="img" aria-label="Photo of three smiling business people in suits in front of city lights">
  <h1 class="hero-title" style="top:441px">Morbi Tristique Senectus</h1>
  <p class="hero-sub" style="top:539px">Pellentesque habitant morbi tristique netus et malesuada</p>
  <div class="dots" style="left:576px;top:606px"><i class="on"></i><i></i><i></i><i></i></div>
</section>

<h2 class="intro-title">VARIUS TURPIS SCELISQUE</h2>
<div class="intro-rule"><b></b></div>
<p class="intro-text">Consectetur adipiscing elit. Etiam felis ante, laoreet vel mi commodo, dapibus porta lectus. Sed elementum scelerisque nunc, non accumsan est pretium nec. Nunc ac lacinia diam, in ultrices orci. Lorem ipsum dolor sit amet, consectetur adipiscing elit. Pellentesque habitant morbi tristique senectus et netus et malesuada fames ac turpis egestas. Pellentesque habitant morbi tristique senectus et netus et malesuada fames ac turpis egestas Quisque urna.</p>
<a class="read-more">Read more &rarr;</a>

<div class="tabs">
  <div class="tab tab-news">NEWS</div>
  <div class="tab tab-awards">REVIEWS &amp; AWARDS</div>
</div>
<div class="news-box">
  <div class="news-item first" style="top:30px">
    <div class="news-thumb" role="img" aria-label="News thumbnail of a boat on water" style="background:linear-gradient(#8a9aa8,#4f5d68)"></div>
    <div class="news-body">
      <h4>Consectetur adipiscing Proin eu ligula</h4>
      <small>Posted on Dec 19th 2013</small>
      <p>Vestibulum nec semper dolor. Fusce in lectus ut libero convallis auctor Suspndisse viverra.</p>
    </div>
  </div>
  <div class="news-sep"></div>
  <div class="news-item" style="top:150px">
    <div class="news-thumb" role="img" aria-label="News thumbnail portrait" style="background:linear-gradient(#b9875a,#5a3a22)"></div>
    <div class="news-body">
      <h4>Consectetur adipiscing Proin eu ligula</h4>
      <small>Posted on Dec 19th 2013</small>
      <p>Vestibulum nec semper dolor. Fusce in lectus ut libero convallis auctor. Susendisse viverra nisi quis nisi ultrices sollicitudin.</p>
    </div>
  </div>
</div>

<section class="feature" role="img" aria-label="Dark background photo of office towers">
  <h2 class="feature-title">FEATURE PROJECTS</h2>
  <h3 class="feature-sub">Lectus Scelerisque</h3>
  <div class="feature-text">
    <p>Consectetur adipiscing elit. Etiam felis ante, laoreet vel mi commodo, dapibus porta lectus scelerisque.</p>
    <p>Consectetur adipiscing elit. Etiam felis ante, laoreet vel mi commodo, dapibus porta lectus scelerisqu nunc accumsan est pretium nec.</p>
  </div>
  <div class="dots" style="left:150px;top:380px"><i class="on"></i><i></i><i></i><i></i></div>
  <div class="feature-media" role="img" aria-label="Photo of red-roofed villas among green trees beside the sea"></div>
</section>

<div class="quote-mark">&ldquo;</div>
<p class="quote-text">Pellentesque habitant morbi tristique senectus et netus et mesuada fames ac turpis egestas. Pellenue habitant morbi tristique senectus et netus et malesuada fames ac turpis egestas Quisque urna mi, faucibus at magna vel, venenatis ornare sem &nbsp;Pellentesque habitant morbi tristique senectus et netus et malesuada fames ac turpis egestas.</p>
<div class="quote-rule"></div>
<svg class="quote-notch" width="20" height="11" viewBox="0 0 20 11"><path d="M0 0L10 10L20 0" fill="var(--paper)" stroke="#d0d0d0"/></svg>
<div class="avatar" role="img" aria-label="Portrait photo of the client"></div>
<div class="quote-name">Consectetur Adipiscing</div>
<div class="quote-role">Lorem ipsum</div>
<div class="rings"><i class="on"></i><i></i><i></i><i></i></div>

<footer class="site-footer">
  <div class="footer-col" style="left:150px">
    <h5>Our Services</h5>
    <ul>
      <li>Consectetur adipiscing</li>
      <li>Etiam felis ante laoreet</li>
      <li>Commodo dapibus porta</li>
      <li>Lectus Sed elementum</li>
      <li>Scelerisque accumsan</li>
    </ul>
  </div>
  <div class="footer-divider" style="left:333px"></div>
  <div class="footer-col" style="left:365px">
    <h5>Condimentum est</h5>
    <ul>
      <li>Pellentesque habitant morbi</li>
      <li>tristique senectus et netus et</li>
      <li>malesuada fames ac turpis</li>
      <li>egestas. Pellentesque</li>
      <li>habitant morbi tristique</li>
    </ul>
  </div>
  <div class="footer-divider" style="left:567px"></div>
  <div class="footer-col subscribe" style="left:603px">
    <h5>Subscribe our newsletter</h5>
    <p>Habitant morbi tristique senectus et netus et malesuada fames ac turpis egestas. Quisque urna mi, faucibus at magna vel, venenatis ornare sem.</p>
  </div>
  <div class="sub-input" style="left:614px">Enter your email here</div>
  <div class="sub-btn" style="left:957px">SUBSCRIBE</div>
</footer>
<div class="bottom-bar">
  <span>Vensol Holdings &copy; All rights reserved.</span>
  <div class="social" style="left:947px;background:#3b5a98"></div>
  <div class="social" style="left:985px;background:#2f9fd8"></div>
  <div class="social" style="left:1022px;background:#d6452f"></div>
</div>

</body>
</html>
```